Security and Technology Website - Bold and Confident, Something Unexpected

Maple Wren Systems is launching its first website and we need a great design to bring our brand to life and generate DTC and B2B leads.

We have a good logo, but I am struggling with the creative vision to bring it all together. While our industry is Alarm Systems and Technology, we want to create a site that is more friendly and less 'typical' than your standard IT sites.

It Must:
1. Appeal to both men and women. The logo is a bit masculine, so the colors and icons must soften this.
2. Feel modern - we need to convey that we we use the latest technology.
3. Feel a bit high-end. We are not a budget solution.
4. Have a distinct iconography and photo treatment.
5. Feel layered - not just a series of stacked horizontal modules.

It Should Not:
1. Feel like your typical IT website.

Here are resources to get you started!
• Staging Site:
https://maple-wren-systems.shopfrontdemo.example/
Password: Piper

•Brand Guide: https://www.layoutboard.example/design/QKRmWpLcT4V/hNbq8Yf2-ZsKeRtDw7xp-QE/edit?utm_content=QKRmWpLcT4V&utm_campaign=designshare&utm_medium=link2&utm_source=sharebutton

• Logo and Fonts and Photos: :https://files.cloudlocker.example/folders/7HtPqWmZc3Kd9RbLx2VnYs8FgJe4UoAiT?usp=sharing

• Design Inspiration (don't feel limited by this): https://www.layoutboard.example/design/QKTnHsVbWe8/p7MfRz31xYqLcKdTu9GNBw/edit?utm_content=QKTnHsVbWe8&utm_campaign=designshare&utm_medium=link2&utm_source=sharebutton

______________

The winner will be asked to provide design files and finished PNGs of the overall design file, backgrounds, photo treatments/frames, and icons.

The winner will likely be engaged for a phase 2 to build out a product page.

Industry/Entity Type

Alarm Systems, Home Theatres, and Commercial IT Networking

Number of Pages Required

1 page

Font styles to use
Sans Serif

Colors
0054AA
0677BA
7BADD7
CADEEF
E8F1F8
0094D4
00A9DD
6FCCEA
C7EBF8
E9F6FB
EB3D1F
EC4F4E
F09395
F8D3D4
FCEDEE

Requirements
Must have
• 1. Appeal to both men and women. The logo is a bit masculine, so the colors and icons must soften this. 2. Feel modern - we need to convey that we we use the latest technology. 3. Feel a bit high-end. We are not a budget solution. 4. Have a distinct iconography and photo treatment. 5. Feel layered - not just a series of stacked horizontal modules.
Should not have
• 1. Should not feel like just another IT website.

```html
<!DOCTYPE html>
<html lang="en">
<head>
<meta charset="utf-8">
<title>Maple Wren Systems</title>
<link href="https://fonts.googleapis.com/css2?family=Orbitron:wght@800;900&family=Roboto:ital,wght@0,400;0,500;0,700;1,400&display=swap" rel="stylesheet">
<style>
:root{
  --blue:#0054AA;
  --blue-deep:#0d4aa6;
  --navy:#1b3584;
  --sky:#00A9DD;
  --pale:#E8F1F8;
  --pale2:#CADEEF;
  --red:#e8201f;
  --text:#555;
  --white:#fff;
  --head:'Orbitron',sans-serif;
  --body:'Roboto',sans-serif;
}
*{margin:0;padding:0;box-sizing:border-box}
html,body{width:1200px;height:5124px;overflow:hidden;background:#fff;font-family:var(--body);color:var(--text)}
.page{position:relative;width:1200px;height:5124px;overflow:hidden}
.abs{position:absolute}
.bg-svg{position:absolute;left:0;width:1200px}

/* top + nav */
.topbar{top:0;left:0;width:1200px;height:32px;background:var(--blue-deep)}
.toplinks{top:0;left:560px;height:32px;display:flex;gap:40px;align-items:center;font-size:11px;font-weight:700;color:#fff}
.quote-btn{top:0;left:915px;width:140px;height:32px;background:var(--red);color:#fff;font-size:11px;font-weight:700;display:flex;align-items:center;justify-content:center}
.navbar{top:32px;left:0;width:1200px;height:68px;background:#fff}
.navlinks{top:32px;left:385px;height:68px;display:flex;gap:34px;align-items:center;font-size:12px;font-weight:500;color:#222}
.navlinks .active{border-left:2px solid var(--red);border-top:2px solid var(--red);padding:2px 6px}
.search{top:60px;left:1038px}
.brand{top:0;left:130px;width:200px;height:210px}
.brand-name{top:80px;left:140px;width:180px;text-align:center;font-family:var(--head);font-weight:900;font-size:18px;line-height:22px;color:var(--blue)}
.brand-mark{top:38px;left:218px;width:24px;height:24px;background:var(--red)}

/* hero */
.hero-title{top:240px;left:143px;width:520px;font-family:var(--head);font-weight:900;font-size:31px;line-height:43px;color:#fff}
.pill{border-radius:24px;color:#fff;font-size:13px;font-weight:700;display:flex;align-items:center;justify-content:center}
.hero-btn{top:445px;left:145px;width:248px;height:44px;background:var(--red)}
.dots{top:606px;left:360px;display:flex;gap:6px}
.dots i{width:12px;height:3px;background:#fff;display:block}
.dots i.on{background:var(--red)}

/* section titles */
.title{font-family:var(--head);font-weight:900;color:var(--navy);text-align:center;letter-spacing:1px}
.title-line{height:3px;background:var(--red)}

/* about */
.about-text{top:832px;left:603px;width:450px;font-size:13.5px;line-height:29px;text-align:justify}
.btn-red{background:var(--red)}
.btn-blue{background:var(--blue)}

/* services */
.card-label{text-align:center;font-size:14px;font-weight:700;color:#222}
.card-sub{text-align:center;font-size:10px;line-height:17px;color:#444}

/* steps */
.step-h{text-align:center;font-size:19px;font-weight:500;color:#222}
.step-p{text-align:center;font-size:12.5px;line-height:23px;color:#777}

/* connect */
.feat-h{font-size:16px;color:#fff}
.feat-p{font-size:11.5px;line-height:23px;color:#e6eefa}
.ring-icon{width:70px;height:70px;border-radius:50%;background:var(--blue-deep);border:3px solid #fff;display:flex;align-items:center;justify-content:center}

/* monitoring */
.monitor{top:3660px;left:145px;width:910px;height:240px;background:var(--red)}

/* partners */
.partner{top:4128px;width:170px;height:100px;background:#fff;border:1px solid #ddd;display:flex;align-items:center;justify-content:center}
.partner.sel{border:3px solid var(--navy)}
.partner span{display:block;width:100px;height:26px;border-radius:4px;background:#d4dbe5}

/* contact */
.field{background:#fff;font-size:9px;color:#555;padding:6px 10px}
.contact-h{font-size:14px;font-weight:500;color:#fff}
.footer{top:5082px;left:0;width:1200px;text-align:center;font-size:11.5px;color:#fff}
</style>
</head>
<body>
<div class="page">

<!-- backgrounds -->
<svg class="bg-svg" style="top:0" height="5124" viewBox="0 0 1200 5124">
  <!-- hero -->
  <polygon points="0,100 670,100 670,530 370,700 0,505" fill="#1450a8"/>
  <rect x="0" y="100" width="18" height="440" fill="var(--red)"/>
  <polygon points="90,560 370,700 1200,560 1200,590 370,720" fill="var(--red)"/>
  <!-- services band -->
  <polygon points="0,1390 830,1175 1200,1340 1200,1935 0,1935" fill="var(--pale)"/>
  <polyline points="0,1370 830,1165 1200,1330" fill="none" stroke="var(--pale2)" stroke-width="8"/>
  <!-- connect band -->
  <polygon points="0,2905 370,2700 1200,2880 1200,3560 0,3620" fill="#0d50b0"/>
  <polyline points="0,2895 370,2690 1200,2870" fill="none" stroke="#1b3584" stroke-width="10"/>
  <!-- testimonial bg -->
  <rect x="0" y="4290" width="1200" height="240" fill="var(--pale)"/>
  <!-- contact -->
  <polygon points="0,4590 860,4440 1200,4560 1200,5124 0,5124" fill="#0d50b0"/>
  <polygon points="0,4590 860,4440 0,4720" fill="var(--red)"/>
</svg>

<!-- header -->
<div class="abs topbar"></div>
<div class="abs toplinks"><span>ABOUT</span><span>CONSULTING</span><span>CONTACT</span></div>
<div class="abs quote-btn">REQUEST A QUOTE</div>
<div class="abs navbar"></div>
<div class="abs navlinks"><span class="active">ELECTRONIC SECURITY</span><span>AUDIO + VIDEO</span><span>NETWORKS + COMMUNICATION</span><span>CABLING</span></div>
<svg class="abs search" width="16" height="16" viewBox="0 0 16 16"><circle cx="6.5" cy="6.5" r="5" fill="none" stroke="var(--red)" stroke-width="2.4"/><line x1="10" y1="10" x2="15" y2="15" stroke="var(--red)" stroke-width="2.6"/></svg>
<svg class="abs brand" viewBox="0 0 200 210"><polygon points="0,0 200,0 200,140 100,210 0,140" fill="#fff"/></svg>
<div class="abs brand-mark"></div>
<div class="abs brand-name">MAPLE WREN SYSTEMS</div>

<!-- hero -->
<h1 class="abs hero-title">PROTECTING WHAT MATTERS MOST WITH CUTTING-EDGE SECURITY SOLUTIONS.</h1>
<div class="abs pill hero-btn">EXPLORE OUR SOLUTIONS</div>
<div class="abs dots"><i></i><i></i><i class="on"></i></div>
<div class="abs" role="img" aria-label="Team meeting on a video conference screen in a modern office" style="top:100px;left:680px;width:520px;height:500px;background:linear-gradient(135deg,#e4e7ea,#a9b2bb 55,#5a5f66)"></div>

<!-- about -->
<div class="abs" style="top:740px;left:140px;width:410px;height:410px;border-radius:50%;border:3px solid var(--blue);background:#fff"></div>
<div class="abs" role="img" aria-label="Portrait of the company founder in a suit and bow tie" style="top:760px;left:160px;width:370px;height:370px;border-radius:50%;background:linear-gradient(180deg,#d6f3f8,#bfe6ee 60%,#2a2f3a)"></div>
<div class="abs title-line" style="top:737px;left:610px;width:170px"></div>
<h2 class="abs title" style="top:748px;left:610px;font-size:40px">ABOUT</h2>
<div class="abs title-line" style="top:795px;left:610px;width:170px;height:2px;background:var(--blue)"></div>
<p class="abs about-text">I founded Maple Wren Systems to bring together technology and honest, reliable service. I'm proud to call Tennessee home and even prouder to help keep its homes and businesses secure. Whether it's protecting or elevating your space, my goal is to make technology work for you. Think of us as your friendly, neighborhood tech expert—here to safeguard what matters most.</p>
<div class="abs pill btn-red" style="top:1030px;left:603px;width:152px;height:44px">READ MORE</div>
<div class="abs pill btn-blue" style="top:1030px;left:762px;width:278px;height:44px">TELL US HOW WE CAN HELP</div>

<!-- services -->
<div class="abs title-line" style="top:1333px;left:468px;width:266px"></div>
<h2 class="abs title" style="top:1340px;left:0;width:1200px;font-size:40px">SERVICES</h2>
<div class="abs title-line" style="top:1392px;left:468px;width:266px;background:var(--navy)"></div>

<svg class="abs" style="top:1458px;left:140px" width="282" height="370" viewBox="0 0 282 370"><path d="M4,70 Q141,-10 278,70 V250 Q141,310 141,368 Q141,310 4,250 Z" fill="#fff" stroke="#dfe4ea" stroke-width="3"/></svg>
<div class="abs" role="img" aria-label="Woman arming a wall-mounted alarm keypad at home" style="top:1460px;left:178px;width:206px;height:240px;border-radius:0 0 103px 103px;background:linear-gradient(160deg,#f3ece4,#b89a84)"></div>
<div class="abs card-label" style="top:1713px;left:140px;width:282px">AFFORDABLE SECURITY</div>
<div class="abs card-sub" style="top:1738px;left:140px;width:282px">For Homes • For Businesses</div>

<svg class="abs" style="top:1458px;left:445px" width="262" height="420" viewBox="0 0 262 420"><path d="M2,80 Q131,-10 260,80 V290 Q131,340 131,418 Q131,340 2,290 Z" fill="var(--red)"/></svg>
<div class="abs" role="img" aria-label="Home theatre room with a large projection screen" style="top:1464px;left:498px;width:206px;height:240px;border-radius:0 0 103px 103px;border:5px solid #fff;background:linear-gradient(160deg,#e9d9bf,#8a6a45 60%,#3b2d20)"></div>
<div class="abs card-label" style="top:1725px;left:445px;width:262px;color:#fff">ENVIABLE ENTERTAINMENT</div>
<div class="abs card-sub" style="top:1752px;left:445px;width:262px;color:#fff;font-size:11px">Home Theatres • Smart Homes<br>Whole Home A/V</div>

<svg class="abs" style="top:1458px;left:780px" width="282" height="370" viewBox="0 0 282 370"><path d="M4,70 Q141,-10 278,70 V250 Q141,310 141,368 Q141,310 4,250 Z" fill="#fff" stroke="#dfe4ea" stroke-width="3"/></svg>
<div class="abs" role="img" aria-label="Business team on a video conference call" style="top:1460px;left:818px;width:206px;height:240px;border-radius:0 0 103px 103px;background:linear-gradient(160deg,#eceff2,#7c8590 60%,#3a3f45)"></div>
<div class="abs card-label" style="top:1713px;left:780px;width:282px">CONNECTED BUSINESSES</div>
<div class="abs card-sub" style="top:1738px;left:780px;width:282px">Conference Systems • Phones<br>Networking • WIFI</div>

<!-- steps -->
<div class="abs title-line" style="top:2055px;left:248px;width:704px"></div>
<h2 class="abs title" style="top:2068px;left:0;width:1200px;font-size:37px;line-height:43px">A SAFER HOME OR BUSINESS<br>IS AS EASY AS 1-2-3</h2>
<div class="abs title-line" style="top:2162px;left:248px;width:520px"></div>

<svg class="abs" style="top:2240px;left:0" width="1200" height="140" viewBox="0 0 1200 140">
  <g font-family="Orbitron,sans-serif" font-weight="900" font-size="110" fill="#fff" stroke="var(--navy)" stroke-width="3">
    <text x="140" y="120">1</text><text x="495" y="120">2</text><text x="868" y="120">3</text>
  </g>
  <circle cx="242" cy="78" r="62" fill="#fff" stroke="var(--red)" stroke-width="3"/><circle cx="242" cy="78" r="48" fill="var(--red)"/>
  <path d="M232,90 l4,-12 l16,-16 l8,8 l-16,16 Z" fill="#fff"/>
  <circle cx="613" cy="78" r="62" fill="#fff" stroke="var(--navy)" stroke-width="3"/><circle cx="613" cy="78" r="48" fill="var(--blue)"/>
  <rect x="598" y="64" width="30" height="28" rx="3" fill="#fff"/><rect x="598" y="64" width="30" height="8" fill="#cfe0f5"/>
  <circle cx="988" cy="78" r="62" fill="#fff" stroke="#c23a5a" stroke-width="3"/><circle cx="988" cy="78" r="48" fill="var(--blue)"/>
  <circle cx="988" cy="78" r="17" fill="#fff"/><path d="M988,68 V79 H996" stroke="var(--blue)" stroke-width="3" fill="none"/>
  <path d="M315,40 Q400,0 490,52" fill="none" stroke="#999" stroke-width="2" stroke-dasharray="3 5"/>
  <path d="M690,110 Q780,150 872,100" fill="none" stroke="#999" stroke-width="2" stroke-dasharray="3 5"/>
</svg>
<div class="abs step-h" style="top:2408px;left:130px;width:240px">Build an Instant Quote</div>
<p class="abs step-p" style="top:2445px;left:130px;width:240px">Our live-estimate builder will guide you through a few questions to help us understand your needs.</p>
<div class="abs step-h" style="top:2408px;left:480px;width:240px">Schedule Installation</div>
<p class="abs step-p" style="top:2445px;left:480px;width:240px">Our trained techs are efficient and friendly. Southern-born and raised (and one mid-westerner), we will respect your home and your schedule.</p>
<div class="abs step-h" style="top:2408px;left:840px;width:225px">Stay Secure 24/7</div>
<p class="abs step-p" style="top:2445px;left:840px;width:225px">Monitor your home through the app, receive instant alerts, and rely on professional monitoring services for emergencies.</p>
<div class="abs pill btn-red" style="top:2580px;left:523px;width:154px;height:44px">GET STARTED</div>

<!-- connect -->
<div class="abs title-line" style="top:2900px;left:345px;width:510px"></div>
<h2 class="abs title" style="top:2918px;left:0;width:1200px;font-size:37px;line-height:43px;color:#fff">CONNECT + PROTECT<br>YOUR WORLD</h2>
<div class="abs title-line" style="top:3010px;left:345px;width:370px"></div>

<svg class="abs" style="top:3090px;left:420px" width="360" height="360" viewBox="0 0 360 360">
  <circle cx="180" cy="180" r="160" fill="none" stroke="#1b3584" stroke-width="12"/>
  <circle cx="180" cy="180" r="130" fill="#fff" stroke="#2e6fd0" stroke-width="14"/>
  <g fill="#0d50b0" stroke="#2e6fd0" stroke-width="3"><circle cx="52" cy="90" r="9"/><circle cx="52" cy="270" r="9"/><circle cx="308" cy="90" r="9"/><circle cx="308" cy="270" r="9"/><circle cx="180" cy="340" r="9"/></g>
</svg>
<div class="abs" style="top:3216px;left:532px;width:18px;height:18px;background:var(--red)"></div>
<div class="abs" style="top:3240px;left:500px;width:200px;text-align:center;font-family:var(--head);font-weight:900;font-size:20px;line-height:26px;color:var(--blue)">MAPLE WREN<br>SYSTEMS</div>

<div class="abs ring-icon" style="top:3078px;left:375px"><svg width="36" height="30" viewBox="0 0 36 30" fill="none" stroke="#fff" stroke-width="2.5"><circle cx="18" cy="15" r="3" fill="#fff"/><path d="M11,8 Q6,15 11,22 M25,8 Q30,15 25,22 M6,3 Q-2,15 6,27 M30,3 Q38,15 30,27"/></svg></div>
<div class="abs feat-h" style="top:3080px;left:120px;width:240px;text-align:right">Entry &amp; Motion Sensors</div>
<p class="abs feat-p" style="top:3108px;left:140px;width:220px;text-align:right">Pair text with an icon to focus on your chosen product, collection, or blog post.</p>

<div class="abs ring-icon" style="top:3074px;left:742px"><svg width="30" height="30" viewBox="0 0 30 30" fill="none" stroke="#fff" stroke-width="2.5"><path d="M6,22 H24 L21,18 V12 A6,6 0 0 0 9,12 V18 Z"/><path d="M12,25 H18"/></svg></div>
<div class="abs feat-h" style="top:3080px;left:833px">Video Doorbells</div>
<p class="abs feat-p" style="top:3108px;left:833px;width:240px">Pair text with an icon to focus on your chosen product, collection, or blog post.</p>

<div class="abs ring-icon" style="top:3295px;left:367px"><svg width="32" height="28" viewBox="0 0 32 28" fill="none" stroke="#fff" stroke-width="2.5"><rect x="3" y="5" width="22" height="12" rx="2"/><path d="M25,9 L30,7 V15 L25,13 M10,17 V25 H4"/></svg></div>
<div class="abs feat-h" style="top:3297px;left:120px;width:225px;text-align:right">Security Cameras</div>
<p class="abs feat-p" style="top:3325px;left:145px;width:205px;text-align:right">Pair text with an icon to focus on your chosen product, collection, or blog post.</p>

<div class="abs ring-icon" style="top:3295px;left:760px"><svg width="30" height="30" viewBox="0 0 30 30" fill="none" stroke="#fff" stroke-width="2.5"><path d="M15,25 C5,18 3,12 7,8 C10,5 13,7 15,10 C17,7 20,5 23,8 C27,12 25,18 15,25 Z"/></svg></div>
<div class="abs feat-h" style="top:3297px;left:853px">Pet-Friendly</div>
<p class="abs feat-p" style="top:3325px;left:853px;width:200px">Pair text with an icon to focus on your chosen product, collection, or blog post.</p>

<div class="abs" style="top:3436px;left:563px;width:74px;height:74px;border-radius:50%;background:var(--red);border:3px solid #fff;display:flex;align-items:center;justify-content:center"><svg width="28" height="34" viewBox="0 0 28 34" fill="none" stroke="#fff" stroke-width="2.5"><path d="M14,2 C16,10 25,14 24,23 A10,10 0 0 1 4,23 C4,16 9,14 10,8 C12,11 13,13 14,2 Z"/></svg></div>
<div class="abs feat-h" style="top:3525px;left:0;width:1200px;text-align:center">Fire &amp; Carbon Monoxide</div>
<p class="abs feat-p" style="top:3553px;left:450px;width:300px;text-align:center">Pair text with an icon to focus on your chosen product, collection, or blog post.</p>

<!-- monitoring -->
<div class="abs monitor"></div>
<h2 class="abs title" style="top:3720px;left:200px;width:300px;font-size:38px;line-height:46px;color:#fff;text-align:left">24/7<br>MONITORING</h2>
<p class="abs" style="top:3712px;left:572px;width:430px;font-size:13px;line-height:25px;color:#fff">Our team is always on guard. With always-on protection, we'll notify you of any suspicious activity. In emergencies, we'll monitor your local police, fire, or EMS.</p>
<div class="abs pill btn-blue" style="top:3818px;left:572px;width:150px;height:44px">GET STARTED</div>

<!-- partners -->
<div class="abs title-line" style="top:3995px;left:345px;width:510px"></div>
<h2 class="abs title" style="top:4008px;left:0;width:1200px;font-size:38px">SERVICE PARTNERS</h2>
<div class="abs title-line" style="top:4063px;left:345px;width:380px;background:var(--navy)"></div>
<svg class="abs" style="top:4145px;left:75px" width="40" height="66" viewBox="0 0 40 66"><path d="M34,2 L4,33 L34,64" fill="none" stroke="#ccc" stroke-width="2"/></svg>
<div class="abs partner" style="left:150px"><span></span></div>
<div class="abs partner" style="left:333px"><span></span></div>
<div class="abs partner sel" style="left:513px"><span></span></div>
<div class="abs partner" style="left:698px"><span></span></div>
<div class="abs partner" style="left:880px"><span></span></div>
<svg class="abs" style="top:4145px;left:1088px" width="40" height="66" viewBox="0 0 40 66"><path d="M6,2 L36,33 L6,64" fill="none" stroke="#ccc" stroke-width="2"/></svg>

<!-- testimonial -->
<div class="abs" style="top:4348px;left:150px;width:96px;height:96px;border-radius:50%;background:#fff;border:2px solid var(--red)"></div>
<p class="abs" style="top:4344px;left:273px;width:780px;font-size:14px;line-height:29px;font-style:italic;color:#555">Fantastic service!! Used Sentrel and Homebright in the past, and their customer service does not compare to Maple Wren Systems! Installation and set up went smoothly!! It's so convenient to use the apps remotely for the cameras, and arming or unarming the alarm. I'd rate them more than 5 stars if I was able to!</p>
<div class="abs" style="top:4465px;left:273px;font-size:14px;font-weight:700;color:#444">- JENNA M. OAK HOLLOW, TN</div>

<!-- contact -->
<div class="abs title-line" style="top:4640px;left:425px;width:350px"></div>
<h2 class="abs title" style="top:4652px;left:0;width:1200px;font-size:38px;color:#fff">CONTACT US</h2>
<div class="abs title-line" style="top:4708px;left:425px;width:300px"></div>
<div class="abs contact-h" style="top:4767px;left:183px">Get In Touch:</div>
<div class="abs field" style="top:4802px;left:186px;width:267px;height:30px">NAME :</div>
<div class="abs field" style="top:4802px;left:463px;width:265px;height:30px">PHONE :</div>
<div class="abs field" style="top:4843px;left:186px;width:542px;height:30px">EMAIL :</div>
<div class="abs field" style="top:4884px;left:186px;width:542px;height:70px">MESSAGE :</div>
<div class="abs pill btn-red" style="top:4968px;left:648px;width:80px;height:28px;font-size:11px;border:1px solid #fff">SUBMIT</div>

<div class="abs contact-h" style="top:4767px;left:797px">Contact Information</div>
<svg class="abs" style="top:4806px;left:797px" width="34" height="34" viewBox="0 0 34 34"><circle cx="17" cy="17" r="16" fill="#fff"/><path d="M17,26 C12,19 11,16 11,14 A6,6 0 0 1 23,14 C23,16 22,19 17,26 Z" fill="none" stroke="var(--navy)" stroke-width="2"/><circle cx="17" cy="14" r="2" fill="var(--navy)"/></svg>
<div class="abs" style="top:4808px;left:848px;font-size:10.5px;line-height:16px;color:#fff">482 Harbor Ridge Rd. Suite 2-210<br>Fairbrook, TN 37990</div>
<svg class="abs" style="top:4855px;left:797px" width="34" height="34" viewBox="0 0 34 34"><circle cx="17" cy="17" r="16" fill="var(--red)" stroke="#fff" stroke-width="2"/><path d="M12,10 L15,10 L16,14 L14,15 Q16,19 19,20 L20,18 L24,19 L24,22 Q17,24 11,14 Z" fill="#fff"/></svg>
<div class="abs" style="top:4864px;left:848px;font-size:14px;color:#fff">615.555.0142</div>
<div class="abs" style="top:4915px;left:800px;display:flex;gap:8px">
  <span style="width:26px;height:26px;border-radius:50%;background:#fff;display:block"></span>
  <span style="width:26px;height:26px;border-radius:50%;background:var(--red);display:block"></span>
  <span style="width:26px;height:26px;border-radius:50%;background:#fff;display:block"></span>
  <span style="width:26px;height:26px;border-radius:50%;background:#fff;display:block"></span>
</div>
<div class="abs footer">Copyrights © 2024, Companyname. All Rights Reserved. &nbsp;|&nbsp; Privacy policy &nbsp;|&nbsp; Terms of Use</div>

</div>
</body>
</html>
```